Valdane Companies Business Card Design

We need a new business card for our Private Equity Real Estate Development firm, “Valdane” and our EB-5 regional center “Thornmere Regional Center” on one card. We prefer a design that is simple, elegant, and represents the luxury products we design and build as well as the financial security and stability our successful history has produced. We are an industry leader in our field and 3rd generation family business that has evolved into an institutional quality investment platform. Considered design size is standard business card dimensions (3.5 x 2 inches with an additional 1/8 inch space for design elements or backgrounds that extend beyond the finished size of your piece.

Target Market(s)

• High net worth individuals
• Highly skilled technical workers and physicians in the US seeking investment-based immigration opportunities
• Sophisticated private equity investors
• Intermediary partners include domestic attorneys and investment brokers, as well as international agent networks
• US real estate developers

Industry/Entity Type

Finance

Contact Information for Business Card

(Providing placeholder info for personal information, please design for longer character spaces, longer names and addresses etc..)
• Logo for Valdane
• Logo for Thornmere Regional Center
• Full name: Marcus Valdane
• Job title: CEO
• Email address: mvaldane@valdanecompanies.com
• Cell phone number: +1.555.314.2287
• Office number +1.555.628.4410
• Office address: Larkfield Court 5, 4817 Vista Orilla, Corlane Hills, OR.
• Website: www.valdanecompanies.com

Font styles to use
Serif
Sans Serif

Colors
ec1f27
ffffff
000000

Requirements
Must have
• • Logo for Valdane
• • Logo for Thornmere Regional Center
• - Use rounded corners
• (See .ai file included for logos)
Nice to have
• • Simple, elegant design
• • Aesthetically compatible with our website design (www.valdanecompanies.com)
• • Color palette including but not limited to white, black, and red (as per logos)
Should not have
• - Not too much red color
• - Do not stack both logos on top of each other

```html
<!DOCTYPE html>
<html lang="en">
<head>
<meta charset="utf-8">
<title>Valdane Companies Business Card</title>
<link rel="stylesheet" href="https://fonts.googleapis.com/css2?family=Libre+Baskerville:wght@400;700&display=swap">
<style>
  :root {
    --brand-red: #a11c30;
    --ink: #1c1c1c;
    --ink-soft: #2a2a2a;
    --paper: #ffffff;
    --stage: #e6e6e6;
    --stripe-dark: #2b2b2b;
  }
  * { box-sizing: border-box; margin: 0; padding: 0; }
  html, body {
    width: 1200px;
    height: 1000px;
    overflow: hidden;
    background: var(--stage);
    font-family: "Libre Baskerville", Georgia, serif;
  }
  .stage {
    position: relative;
    width: 1200px;
    height: 1000px;
  }
  .card {
    position: absolute;
    left: 250px;
    width: 700px;
    height: 400px;
    border-radius: 26px;
    overflow: hidden;
  }

  /* Front */
  .card--front {
    top: 70px;
    background: var(--brand-red);
    display: flex;
    flex-direction: column;
    align-items: center;
    justify-content: center;
  }
  .wordmark {
    font-weight: 700;
    text-transform: uppercase;
    text-align: center;
    line-height: 1;
  }
  .card--front .wordmark { color: var(--paper); }
  .wordmark__name { display: block; font-size: 58px; letter-spacing: 2px; }
  .wordmark__sub { display: block; font-size: 18px; letter-spacing: 12px; margin-top: 12px; padding-left: 12px; }

  /* Back */
  .card--back {
    top: 530px;
    background: var(--paper);
  }
  .back__band {
    position: absolute;
    left: 0; top: 0; bottom: 0;
    width: 34px;
    background: var(--brand-red);
  }
  .back__stripe {
    position: absolute;
    left: 34px; top: 0; bottom: 0;
    width: 5px;
    background: var(--stripe-dark);
  }
  .back__main {
    position: absolute;
    left: 92px;
    top: 48px;
  }
  .card--back .wordmark { color: var(--ink); text-align: left; }
  .card--back .wordmark__name { font-size: 42px; letter-spacing: 1px; }
  .card--back .wordmark__sub { font-size: 13px; letter-spacing: 9px; margin-top: 8px; padding-left: 96px; }

  .person { margin-top: 38px; }
  .person__name {
    color: var(--brand-red);
    font-weight: 700;
    font-size: 19px;
    text-transform: uppercase;
    letter-spacing: 0.5px;
  }
  .person__title {
    font-size: 11px;
    color: var(--ink-soft);
    margin-top: 2px;
  }
  .contact {
    list-style: none;
    margin-top: 14px;
    font-size: 14px;
    color: var(--ink);
    line-height: 1.45;
  }
  .contact li { display: flex; align-items: center; gap: 7px; white-space: nowrap; }
  .contact svg { width: 11px; height: 11px; fill: var(--brand-red); flex: none; }
  .contact .accent { color: var(--brand-red); }

  .partner {
    position: absolute;
    right: 56px;
    top: 200px;
    display: flex;
    align-items: center;
    gap: 10px;
    color: var(--brand-red);
    font-weight: 700;
  }
  .partner__mark {
    width: 30px; height: 30px;
    background: var(--brand-red);
    border-radius: 3px;
  }
  .partner__name { font-size: 20px; text-transform: uppercase; line-height: 1.05; }
  .partner__name small { display: block; font-size: 9px; letter-spacing: 2.4px; margin-top: 3px; }
</style>
</head>
<body>
<main class="stage">

  <section class="card card--front" aria-label="Card front">
    <p class="wordmark">
      <span class="wordmark__name">Valdane</span>
      <span class="wordmark__sub">Capital</span>
    </p>
  </section>

  <section class="card card--back" aria-label="Card back">
    <div class="back__band"></div>
    <div class="back__stripe"></div>

    <div class="back__main">
      <p class="wordmark">
        <span class="wordmark__name">Valdane</span>
        <span class="wordmark__sub">Capital</span>
      </p>

      <div class="person">
        <p class="person__name">Marcus Valdane</p>
        <p class="person__title">CEO</p>
      </div>

      <ul class="contact">
        <li class="address">Larkfield Court 5, 4817</li>
        <li class="address">Vista Orilla, Corlane Hills, OR.</li>
        <li>
          <svg viewBox="0 0 24 24" aria-hidden="true"><path d="M6.6 10.8a15.1 15.1 0 0 0 6.6 6.6l2.2-2.2c.3-.3.7-.4 1-.2 1.1.4 2.3.6 3.6.6.6 0 1 .4 1 1V20c0 .6-.4 1-1 1A17 17 0 0 1 3 4c0-.6.4-1 1-1h3.5c.6 0 1 .4 1 1 0 1.3.2 2.5.6 3.6.1.3 0 .7-.2 1z"/></svg>
          +1.555.314.2287
        </li>
        <li>
          <svg viewBox="0 0 24 24" aria-hidden="true"><path d="M7 1h10a2 2 0 0 1 2 2v18a2 2 0 0 1-2 2H7a2 2 0 0 1-2-2V3a2 2 0 0 1 2-2zm0 3v14h10V4zm5 15.5a1.2 1.2 0 1 0 0 2.4 1.2 1.2 0 0 0 0-2.4z"/></svg>
          +1.555.628.4410
        </li>
        <li>
          <svg viewBox="0 0 24 24" aria-hidden="true"><path d="M2 5h20v14H2zm2 2v.5l8 5 8-5V7zm0 2.8V17h16V9.8l-8 5z"/></svg>
          mvaldane@valdanecompanies.com
        </li>
        <li>
          <svg viewBox="0 0 24 24" aria-hidden="true"><path d="M12 2a10 10 0 1 0 0 20 10 10 0 0 0 0-20zm6.9 6h-3a15.6 15.6 0 0 0-1.4-3.6A8 8 0 0 1 18.9 8zM12 4c.8 1.2 1.5 2.5 1.9 4h-3.8c.4-1.5 1.1-2.8 1.9-4zM4.3 14a8.2 8.2 0 0 1 0-4h3.4a16.5 16.5 0 0 0 0 4zm.8 2h3a15.6 15.6 0 0 0 1.4 3.6A8 8 0 0 1 5.1 16zm3-8h-3a8 8 0 0 1 4.4-3.6C8.8 5.5 8.4 6.7 8.1 8zM12 20c-.8-1.2-1.5-2.5-1.9-4h3.8c-.4 1.5-1.1 2.8-1.9 4zm2.3-6H9.7a14.7 14.7 0 0 1 0-4h4.6a14.7 14.7 0 0 1 0 4zm.2 5.6c.6-1.1 1.1-2.3 1.4-3.6h3a8 8 0 0 1-4.4 3.6zm1.8-5.6a16.5 16.5 0 0 0 0-4h3.4a8.2 8.2 0 0 1 0 4z"/></svg>
          <span>www.<span class="accent">valdanecompanies</span>.com</span>
        </li>
      </ul>
    </div>

    <div class="partner">
      <span class="partner__mark" aria-hidden="true"></span>
      <p class="partner__name">Thornmere<small>Regional Center</small></p>
    </div>
  </section>

</main>
</body>
</html>
```